Professional BIO Template with photo and logo

Hello,
I need a professional Bio template developed via Microsoft WORD ASAP!!!!! I would like to just be able to add the text I need to add. So resize-able text boxes. Potentially able to adjust the font. These are the things I need added it to include.
Head shot (attached)
Text Box for Name
Text Box for phone number
Text box for email
KVT Logo (attached)
Maybe a blue banner at the top or some background boxes that are blue or grey. Here are the pantone colors that our company uses.

CORE COLOR
100c 91m 17y 6k 38r 58g 128b Hex #263A80 Pantone 7687 C

CORE CONTRAST COLOR
36c 29m 28y 0k 168r 168g 170b Hex #669999 Pantone Cool Gray 6C

I also attached some examples of what we have been looking at. Instead of green add the blue...instead of black maybe just be white.

Thank you

```html
<!DOCTYPE html>
<html lang="en">
<head>
<meta charset="utf-8">
<title>Dana Whitfield – Bio</title>
<link rel="stylesheet" href="https://fonts.googleapis.com/css2?family=Poppins:wght@300;400;500;700&display=swap">
<style>
  :root {
    --band-dark: #0a4f9e;
    --band-mid: #0f62c4;
    --band-light: #1a78e0;
    --accent: #0077e0;
    --ink: #222222;
    --frame: #ececec;
    --photo-tone: #5a5a5c;
    --white: #ffffff;
    --muted: #444444;
  }
  * { margin: 0; padding: 0; box-sizing: border-box; }
  html, body { width: 837px; height: 1200px; overflow: hidden; background: var(--white); }
  body { font-family: "Poppins", sans-serif; color: var(--ink); position: relative; }

  .header-band {
    position: absolute; left: 0; top: 0; width: 837px; height: 233px;
    background: linear-gradient(100deg, var(--band-light) 0%, var(--band-mid) 45%, var(--band-dark) 100%);
  }
  .brand {
    position: absolute; left: 69px; top: 16px; width: 101px; height: 74px;
    display: flex; align-items: center; justify-content: center; gap: 8px;
    color: var(--white); font-weight: 700; font-size: 24px; letter-spacing: 2px;
  }
  .brand-square { width: 12px; height: 12px; background: var(--white); }

  .headshot-frame {
    position: absolute; left: 67px; top: 113px; width: 213px; height: 242px;
    background: var(--frame);
  }
  .headshot {
    position: absolute; left: 7px; top: 8px; width: 199px; height: 226px;
    background: radial-gradient(ellipse at 50% 40%, #7a7a7c 0%, var(--photo-tone) 60%, #3d3d40 100%);
  }

  .name {
    position: absolute; left: 303px; top: 112px;
    font-size: 38px; font-weight: 700; color: var(--white); letter-spacing: 0.3px;
  }
  .designation {
    position: absolute; left: 306px; top: 161px;
    font-size: 17px; font-weight: 400; color: var(--white);
  }

  .contact { position: absolute; left: 307px; display: flex; align-items: center; gap: 11px;
    font-size: 19px; font-weight: 500; color: var(--ink); }
  .contact svg { width: 25px; height: 25px; }
  .contact-phone { top: 257px; }
  .contact-email { top: 302px; }

  .section-title {
    position: absolute; left: 75px; top: 394px;
    font-size: 33px; font-weight: 400; color: var(--ink);
    display: flex; align-items: center; gap: 16px;
  }
  .section-title::after {
    content: ""; width: 84px; height: 2px; background: var(--accent);
  }

  .bio-text {
    position: absolute; left: 75px; width: 715px;
    font-size: 14.2px; line-height: 24px; font-weight: 400; color: var(--muted);
  }
  .bio-1 { top: 453px; }
  .bio-2 { top: 580px; }
  .bio-3 { top: 935px; left: 78px; }

  .highlight {
    position: absolute; left: 75px; top: 711px; width: 695px; height: 186px;
    background: var(--accent); border-radius: 2px; padding: 30px 22px 0 35px; color: var(--white);
  }
  .highlight-lead { font-size: 16.3px; font-weight: 700; line-height: 24px; }
  .highlight-body { font-size: 16.6px; font-weight: 300; line-height: 24px; margin-top: 3px; }

  .footer-fade {
    position: absolute; left: 0; top: 1060px; width: 837px; height: 74px;
    background: linear-gradient(180deg, rgba(240,240,242,0) 0%, #efeff1 100%);
  }
  .footer-note {
    position: absolute; left: 0; top: 1154px; width: 827px; text-align: center;
    font-size: 10.5px; color: var(--muted);
  }
</style>
</head>
<body>
  <div class="header-band" role="img" aria-label="Blue-toned city skyline photograph"></div>

  <div class="brand"><span class="brand-square"></span>KVT</div>

  <div class="headshot-frame">
    <div class="headshot" role="img" aria-label="Headshot portrait of Dana Whitfield"></div>
  </div>

  <h1 class="name">DANA WHITFIELD</h1>
  <p class="designation">POST DESIGNATION</p>

  <div class="contact contact-phone">
    <svg viewBox="0 0 24 24" fill="none" stroke="#1a78e0" stroke-width="1.2" stroke-linejoin="round">
      <path d="M5 2.5l3.2 3.6-1.8 2.4c1.4 3 3.8 5.6 6.9 7.3l2.4-1.8 3.7 3.1-1.9 3.4C11 19.5 4.5 13 1.7 4.7z"/>
    </svg>
    <span>(555) 014-2290</span>
  </div>
  <div class="contact contact-email">
    <svg viewBox="0 0 24 24" fill="none" stroke="#1a78e0" stroke-width="1.2">
      <rect x="1.5" y="4.5" width="21" height="15"/>
      <path d="M1.5 4.5l10.5 9 10.5-9M1.5 19.5l7.5-7.5M22.5 19.5L15 12"/>
    </svg>
    <span>mail.dwhitfield@example.com</span>
  </div>

  <h2 class="section-title">ABOUT ME</h2>

  <p class="bio-text bio-1">Lorem ipsum dolor sit amet, consectetur adipiscing elit, sed do eiusmod tempor incididunt ut labore et dolore magna aliqua. Ut enim ad minim veniam, quis nostrud exercitation ullamco laboris nisi ut aliquip ex ea commodo consequat. Duis aute irure dolor in reprehenderit in voluptate velit esse cillum dolore eu fugiat nulla pariatur. Excepteur sint occaecat cupidatat non proident, sunt in culpa qui officia des</p>

  <p class="bio-text bio-2">Sed ut perspiciatis unde omnis iste natus error sit voluptatem accusantium doloremque laudantium, totam rem aperiam, eaque ipsa quae ab illo inventore veritatis et quasi architecto beatae vitae dicta sunt explicabo. vatem quia voluptas sit aspernatur aut odit aut fugit, sed quia consequuntur magni dolores eos qui ratione voluptatem sequi nesciunt. Neque porro quisquam est, qui dolore</p>

  <div class="highlight">
    <p class="highlight-lead">Adipisci velit, sed quia non numquam eius modi tempora incidunt ut labore et dolore magnam aliquam quaerat voluptatem.</p>
    <p class="highlight-body">Ut enim ad minima veniam, quis nostrum exercitationem ullam corporis suscipit laboriosam, nisi ut aliquid ex ea commodi consequatur? Quis autem vel eum iure reprehenderit qui in ea voluptate velit esse quam nihil molestiae consequa</p>
  </div>

  <p class="bio-text bio-3">Sed ut perspiciatis unde omnis iste natus error sit voluptatem accusantium doloremque laudantium, totam rem aperiam, eaque ipsa quae ab illo inventore veritatis et quasi architecto beatae vitae dicta sunt explicabo. Nemo enim ipsam voluptatem quia t, sed quia consequuntur magni dolores eos qui ratione voluptatem sequi nesciunt. Neque porro quisquam est, qui dolorem ipsum quia dolor sit amet, consectetur, adipisci velit, sed quia non numquam eius modi tempora incidunt ut labore et dolore magnam aliquam quaerat voluptatem. Ut enim ad minima veniam, quis nostrum exercitationem ullam corporis</p>

  <div class="footer-fade" role="img" aria-label="Faint grey city skyline fading into the page"></div>
  <p class="footer-note">© 2022 Company Name | All Rights Reserved</p>
</body>
</html>
```